Dynamic Business Card for Sports Supplements Company

Hi! I'm looking for an awesome business card to match my existing sports supplement company. I have uploaded my current company logo and screenshot of the front page of my website.

I would like to have something dynamic and interesting and utilize the colors in the website - the reds and purples

The business card should be double sided and focus on a unique eye-catching design on the back and include all the relevant company info.

Most importantly, it should say somewhere: "Sign up on our website for a coupon code."

Target Market(s)

Mostly for women gym goers but it shouldn't be too feminine. It should be in keeping with the website design. It should flow and clearly be connected to it

Industry/Entity Type

Business

Contact Information for Business Card

Lorraine K. Vestal
CEO
LVestal@Quorvanexco.com
www.quorvanexco.com
555.417.3820
P.O. Box 47315
Halden, Westmark 00000

Sign up on our website for a coupon code

Font styles to use
Serif
Sans Serif
Other font styles liked:
• Novecento font family and "Quorvanex" is in AR Destine font

Requirements
Must have
• One side should be a bold Quorvanex logo design. Even just the symbol itself may be o.k. (see attached file)

```html
<!DOCTYPE html>
<html lang="en">
<head>
<meta charset="utf-8">
<title>Quorvanex Business Card</title>
<link rel="stylesheet" href="https://fonts.googleapis.com/css2?family=Open+Sans:wght@400;600;700&display=swap">
<style>
  :root {
    --backdrop: #3b3230;
    --card-dark: #2b3140;
    --card-dark-deep: #1f2431;
    --brand-red: #ec1c24;
    --text-light: #ffffff;
    --text-soft: #e3e6ee;
  }
  * { margin: 0; padding: 0; box-sizing: border-box; }
  html, body {
    width: 1200px; height: 844px; overflow: hidden;
    background: var(--backdrop);
    font-family: "Open Sans", Arial, sans-serif;
  }
  .stage {
    position: relative; width: 1200px; height: 844px;
    display: flex; align-items: center; justify-content: center; gap: 40px;
  }
  .card {
    position: relative; width: 540px; height: 309px; overflow: hidden;
    background: linear-gradient(160deg, var(--card-dark) 0%, var(--card-dark-deep) 100%);
    box-shadow: 0 10px 30px rgba(0,0,0,0.45);
  }

  /* Front side */
  .front__band {
    position: absolute; left: 0; top: 0; width: 400px; height: 118px;
    background: var(--brand-red);
  }
  .front__brand {
    position: absolute; right: 28px; top: 132px;
    display: flex; align-items: center; gap: 8px;
  }
  .front__brand-dot {
    width: 20px; height: 20px; border-radius: 50%;
    background: var(--brand-red); border: 3px solid var(--text-light);
  }
  .front__brand-name {
    color: var(--text-light); font-weight: 700; font-size: 22px;
    letter-spacing: 1px; text-transform: uppercase;
  }
  .front__details {
    position: absolute; left: 36px; top: 136px; color: var(--text-soft);
  }
  .person__name { color: var(--text-light); font-weight: 700; font-size: 17px; }
  .person__title { font-size: 12px; margin-bottom: 12px; }
  .address { font-size: 13px; line-height: 1.35; margin-bottom: 12px; }
  .contact { list-style: none; font-size: 13px; line-height: 1.5; }
  .contact li { display: flex; align-items: center; gap: 8px; }
  .contact svg { width: 12px; height: 12px; fill: var(--brand-red); flex: none; }

  /* Back side */
  .back {
    display: flex; flex-direction: column; align-items: center; justify-content: center;
    text-align: center; color: var(--text-light);
  }
  .back__brand { display: flex; align-items: center; gap: 12px; }
  .back__brand-dot { width: 30px; height: 30px; background: var(--brand-red); }
  .back__brand-name {
    font-weight: 700; font-size: 38px; letter-spacing: 2px; text-transform: uppercase;
  }
  .back__tagline {
    margin-top: 6px; font-size: 11px; letter-spacing: 3px; text-transform: uppercase;
    color: var(--text-soft);
  }
  .back__offer { margin-top: 22px; font-size: 14px; color: var(--text-soft); }
</style>
</head>
<body>
<main class="stage">
  <section class="card front" aria-label="Business card front">
    <div class="front__band"></div>
    <div class="front__brand">
      <span class="front__brand-dot"></span>
      <span class="front__brand-name">Quorvanex</span>
    </div>
    <div class="front__details">
      <p class="person__name">Lorraine K. Vestal</p>
      <p class="person__title">CEO</p>
      <p class="address">P.O. Box 47315<br>Halden, Westmark 00000</p>
      <ul class="contact">
        <li>
          <svg viewBox="0 0 24 24" aria-hidden="true"><path d="M6.6 10.8a15 15 0 0 0 6.6 6.6l2.2-2.2a1 1 0 0 1 1-.25 11 11 0 0 0 3.6.6 1 1 0 0 1 1 1V20a1 1 0 0 1-1 1A17 17 0 0 1 3 4a1 1 0 0 1 1-1h3.5a1 1 0 0 1 1 1 11 11 0 0 0 .6 3.6 1 1 0 0 1-.25 1z"/></svg>
          555.417.3820
        </li>
        <li>
          <svg viewBox="0 0 24 24" aria-hidden="true"><path d="M2 5h20v14H2z M2 5l10 8 10-8" stroke="#2b3140" stroke-width="2"/></svg>
          LVestal@Quorvanexco.com
        </li>
        <li>
          <svg viewBox="0 0 24 24" aria-hidden="true"><circle cx="12" cy="12" r="10"/><path d="M2 12h20M12 2c3 3 3 17 0 20M12 2c-3 3-3 17 0 20" stroke="#2b3140" stroke-width="1.6" fill="none"/></svg>
          www.quorvanexco.com
        </li>
      </ul>
    </div>
  </section>

  <section class="card back" aria-label="Business card back">
    <div class="back__brand">
      <span class="back__brand-dot"></span>
      <span class="back__brand-name">Quorvanex</span>
    </div>
    <p class="back__tagline">Your Training Ally</p>
    <p class="back__offer">Sign up on our website for a coupon code</p>
  </section>
</main>
</body>
</html>
```